Kelvaro.ch is looking for business card letterhead and envelope C5 with WOW effect

We need a strong business card for our company Kelvaro.ch, logo is available. You want a black or dark background on which the logo Stark r% 26 # 252; appears. Letterhead and envelope in C5 format should be in a similar design, but does not have to be We need a strong business card for our company Kelvaro.ch, logo is available. A black or dark background is desired, on which the logo Stark comes across. The letterhead and the envelope in C5 format should have a similar design.

Target Market(s)

Private customers as well as entrepreneurs

Contact Information for Business Card

E-mail: info@kelvaro-example.ch
Web.www.Kelvaro-example.ch
Tel: +41 ( 0 ) 79 482 6037
Adresse:
Lindenweg 14
9406 Tarnbach

Hier kann man Icons verwenden für Email,Tel und Adressse

Font styles to use
Other font styles liked:
• Dubai,bold

Colors

Designer to choose colors to be used in the design.

Requirements
Must have
• WOW effect
Nice to have
• R% 26 # 252; back business card with our service listings. - VEHICLE LABELING - SHOP WINDOW LABELING - STICKERS AND MUCH MORE ... in red color

```html
<!DOCTYPE html>
<html lang="en">
<head>
<meta charset="utf-8">
<title>Kelvaro.ch – Business Card</title>
<link rel="stylesheet" href="https://fonts.googleapis.com/css2?family=Arimo:wght@400;700&display=swap">
<style>
  :root {
    --backdrop: #2a2a2c;
    --card: #121212;
    --card-edge: #1c1c1c;
    --accent: #f8c31a;
    --text-light: #f2f2f2;
    --text-soft: #d9d9d9;
    --divider: #4a4a4a;
  }
  * { box-sizing: border-box; margin: 0; padding: 0; }
  html, body { width: 1200px; height: 900px; overflow: hidden; }
  body {
    background: var(--backdrop);
    font-family: "Arimo", Arial, sans-serif;
    position: relative;
  }
  .card {
    position: absolute;
    left: 330px;
    width: 540px;
    height: 310px;
    background: linear-gradient(135deg, var(--card-edge), var(--card) 60%);
    overflow: hidden;
    box-shadow: 0 10px 30px rgba(0,0,0,0.45);
  }
  .card::after {
    content: "";
    position: absolute;
    left: 0; right: 0; bottom: 0;
    height: 9px;
    background: var(--accent);
  }
  .card--front { top: 100px; }
  .card--back { top: 480px; }

  /* Brand lockup */
  .brand {
    display: flex;
    align-items: center;
    gap: 14px;
  }
  .brand__mark {
    width: 34px;
    height: 34px;
    background: var(--accent);
  }
  .brand__name {
    font-weight: 700;
    color: var(--text-light);
    text-transform: uppercase;
    letter-spacing: 1px;
  }

  /* Front */
  .card--front .brand {
    position: absolute;
    left: 0; right: 0;
    top: 92px;
    justify-content: center;
  }
  .card--front .brand__mark { width: 46px; height: 46px; }
  .card--front .brand__name { font-size: 40px; }
  .services {
    position: absolute;
    left: 0; right: 0;
    top: 184px;
    text-align: center;
    color: var(--accent);
    font-weight: 700;
    font-size: 13.5px;
    line-height: 1.6;
    text-transform: uppercase;
  }
  .services__sep { margin: 0 8px; }

  /* Back */
  .card--back .brand {
    position: absolute;
    left: 40px;
    top: 110px;
  }
  .card--back .brand__name { font-size: 26px; }
  .card--back .divider {
    position: absolute;
    left: 290px;
    top: 78px;
    width: 1px;
    height: 120px;
    background: var(--divider);
  }
  .contact {
    position: absolute;
    left: 318px;
    top: 96px;
    list-style: none;
  }
  .contact__item {
    display: flex;
    align-items: center;
    gap: 10px;
    color: var(--text-light);
    font-size: 15.5px;
    line-height: 1;
    margin-bottom: 11px;
  }
  .contact__icon { width: 18px; height: 18px; flex: none; }
  .address {
    position: absolute;
    left: 0; right: 0;
    top: 250px;
    text-align: center;
    color: var(--text-soft);
    font-size: 17px;
  }
</style>
</head>
<body>

  <section class="card card--front" aria-label="Business card front">
    <div class="brand">
      <span class="brand__mark"></span>
      <span class="brand__name">Kelvaro.ch</span>
    </div>
    <p class="services">
      Vehicle labeling<span class="services__sep">|</span>Shop window labeling<br>
      Stickers and much more ...
    </p>
  </section>

  <section class="card card--back" aria-label="Business card back">
    <div class="brand">
      <span class="brand__mark"></span>
      <span class="brand__name">Kelvaro.ch</span>
    </div>
    <span class="divider"></span>
    <ul class="contact">
      <li class="contact__item">
        <svg class="contact__icon" viewBox="0 0 18 18" aria-hidden="true">
          <rect x="1" y="1" width="16" height="16" rx="2" fill="none" stroke="var(--accent)" stroke-width="1.6"/>
          <path d="M6 4.5c-.8.4-1.3 1.2-1 2.4.6 2.6 3 5.3 5.6 6.1 1.2.4 2-.1 2.5-.9l-1.6-1.6-1.3.7c-1.2-.6-2.3-1.7-2.9-2.9l.7-1.3z" fill="var(--accent)"/>
        </svg>
        +41 ( 0 ) 79 482 6037
      </li>
      <li class="contact__item">
        <svg class="contact__icon" viewBox="0 0 18 18" aria-hidden="true">
          <rect x="1" y="3.5" width="16" height="11" fill="var(--accent)"/>
          <path d="M1 3.5l8 6.5 8-6.5" fill="none" stroke="var(--card)" stroke-width="1.4"/>
        </svg>
        info@kelvaro-example.ch
      </li>
      <li class="contact__item">
        <svg class="contact__icon" viewBox="0 0 18 18" aria-hidden="true">
          <circle cx="9" cy="9" r="7.5" fill="none" stroke="var(--accent)" stroke-width="1.6"/>
          <ellipse cx="9" cy="9" rx="3.2" ry="7.5" fill="none" stroke="var(--accent)" stroke-width="1.3"/>
          <path d="M1.5 9h15M3 5h12M3 13h12" stroke="var(--accent)" stroke-width="1.3"/>
        </svg>
        www.Kelvaro-example.ch
      </li>
    </ul>
    <p class="address">Lindenweg 14, 9406 Tarnbach</p>
  </section>

</body>
</html>
```